Brindlewick Solutions Ltd

I'd like to create a company letterhead for the attached logo in word format.

I'd like to emphasis the icon in large translucent state from the left corner and ensure that the letterhead colouring matches the colour palette of the current logo with a contrast so it's clear to see. I've attached a copy of our sister company page on the app for reference.

```html
<!DOCTYPE html>
<html lang="en">
<head>
<meta charset="utf-8">
<title>Brindlewick Solutions Ltd – Letterhead</title>
<link href="https://fonts.googleapis.com/css2?family=Nunito:wght@400;500&display=swap" rel="stylesheet">
<style>
  :root {
    --backdrop: #67696d;
    --paper: #f1f1f1;
    --teal: #48b6a5;
    --teal-faint: rgba(72, 182, 165, 0.12);
    --ink: #555a5e;
  }
  html, body {
    margin: 0;
    width: 1200px;
    height: 803px;
    overflow: hidden;
    background: var(--backdrop);
    font-family: "Nunito", sans-serif;
  }
  .letterhead {
    position: absolute;
    left: 330px;
    top: 20px;
    width: 540px;
    height: 763px;
    background: var(--paper);
    overflow: hidden;
  }
  .brand {
    position: absolute;
    left: 51px;
    top: 57px;
    display: flex;
    align-items: center;
    gap: 8px;
  }
  .brand-dot {
    width: 20px;
    height: 20px;
    border-radius: 50%;
    background: var(--teal);
  }
  .brand-name {
    color: var(--teal);
    font-size: 18px;
    font-weight: 500;
    white-space: nowrap;
  }
  .contact {
    position: absolute;
    top: 60px;
    font-size: 7.6px;
    line-height: 12.3px;
    color: var(--ink);
    font-style: normal;
  }
  .contact-address { left: 334px; }
  .contact-lines { left: 427px; }
  .contact-line {
    display: flex;
    align-items: center;
    gap: 5px;
  }
  .contact-icon {
    width: 7px;
    height: 7px;
    fill: var(--teal);
  }
  .watermark-disc {
    position: absolute;
    left: -80px;
    top: 400px;
    width: 420px;
    height: 420px;
    border-radius: 50%;
    background: var(--teal-faint);
  }
  .footer-band {
    position: absolute;
    left: 0;
    bottom: 0;
    width: 100%;
    height: 26px;
    background: var(--teal);
  }
</style>
</head>
<body>
  <main class="letterhead">
    <div class="watermark-disc" aria-hidden="true"></div>

    <header class="brand">
      <span class="brand-dot" aria-hidden="true"></span>
      <span class="brand-name">Brindlewick Solutions Ltd</span>
    </header>

    <address class="contact contact-address">
      412 Harlow Street<br>
      Suite 210<br>
      Fairbrook, IL 60412
    </address>

    <div class="contact contact-lines">
      <div class="contact-line">
        <svg class="contact-icon" viewBox="0 0 10 10" aria-hidden="true"><path d="M2 0.5 L4 2.8 L3 4 C3.8 5.5 4.6 6.3 6 7 L7.2 6 L9.5 8 L8.3 9.5 C4.5 9.3 0.7 5.5 0.5 1.7 Z"/></svg>
        <span>555-014-2290</span>
      </div>
      <div class="contact-line">
        <svg class="contact-icon" viewBox="0 0 10 10" aria-hidden="true"><path d="M0.5 2 H9.5 V8 H0.5 Z M0.5 2 L5 5.5 L9.5 2" fill="var(--teal)" stroke="var(--paper)" stroke-width="0.8"/></svg>
        <span>info@brindlewick.com</span>
      </div>
      <div class="contact-line">
        <svg class="contact-icon" viewBox="0 0 10 10" aria-hidden="true"><circle cx="5" cy="5" r="4.3" fill="none" stroke="var(--teal)" stroke-width="1"/><path d="M0.7 5 H9.3 M5 0.7 C3 3 3 7 5 9.3 M5 0.7 C7 3 7 7 5 9.3" fill="none" stroke="var(--teal)" stroke-width="0.7"/></svg>
        <span>brindlewick.com</span>
      </div>
    </div>

    <div class="footer-band" aria-hidden="true"></div>
  </main>
</body>
</html>
```